Lorvex Tilo medical cannibis cultivation company

tag - Tilo rise
Lorvex Tilo medical cannabis cultivation - logo is selected- can we please see bold examples with our selection. We are mainly dealing with medical companies and professionals. We would like to be stand out in the crowd with our designs. Welcome any and all attempts. Thanks

Target Market(s)

Medical and Professional

Industry/Entity Type

Medical And Science

Font styles to use
Sans Serif

Colors

Designer to choose colors to be used in the design.

Requirements
Must have
• Bright colour and be bold- Love the teal and magenta that is currently on the dark background design.
Nice to have
• shading and the 3D affect- The shadowed appearance.
Should not have
• Anything related to illegal activity or un professional manners

```html
<!DOCTYPE html>
<html lang="en">
<head>
<meta charset="utf-8">
<title>Lorvex Tilo – Stationery</title>
<link href="https://fonts.googleapis.com/css2?family=Open+Sans:wght@400;600&family=Marcellus&display=swap" rel="stylesheet">
<style>
  :root{
    --teal:#12a6b8;
    --magenta:#e4348a;
    --mauve:#bd6c97;
    --grey:#8a8d92;
    --ink:#3a3a3a;
    --paper:#ffffff;
    --stage:#efefef;
  }
  *{margin:0;padding:0;box-sizing:border-box}
  html,body{width:1200px;height:1200px;overflow:hidden}
  body{background:var(--stage);position:relative;font-family:"Open Sans",sans-serif;color:var(--ink)}
  .sheet{position:absolute}
  .backing{left:93px;top:102px;width:717px;height:926px;background:var(--mauve)}
  .letterhead{left:128px;top:138px;width:717px;height:927px;background:var(--paper);overflow:hidden}
  .brand{position:absolute;text-align:center;font-family:"Marcellus",sans-serif}
  .brand .mark{display:block;margin:0 auto;border:2px solid var(--grey);border-radius:50%}
  .brand .name{display:block;color:var(--teal);line-height:1;white-space:nowrap}
  .brand .tag{display:flex;align-items:center;justify-content:center;gap:4px;color:var(--grey);letter-spacing:2px;text-transform:uppercase;white-space:nowrap}
  .brand .tag::before,.brand .tag::after{content:"";height:1px;background:var(--grey);flex:0 0 26px}
  .letterhead .brand{left:0;right:0;top:24px}
  .letterhead .mark{width:78px;height:78px}
  .letterhead .name{font-size:25px;margin-top:6px}
  .letterhead .tag{font-size:9px;margin-top:1px}
  .letter{position:absolute;left:62px;top:200px;font-size:13px;line-height:24px;white-space:nowrap}
  .letter p{margin-bottom:24px}
  .signoff{position:absolute;left:60px;top:675px;font-size:12.5px}
  .signature{position:absolute;left:60px;top:696px;width:150px;height:42px;background:#e8e8ea;border-radius:6px}
  .letter-foot{position:absolute;left:54px;right:54px;top:856px;text-align:center}
  .letter-foot .company{font-size:12.5px;color:var(--magenta);text-transform:uppercase}
  .letter-foot .rule{position:relative;height:1px;background:#cfcfcf;margin:9px 0 10px}
  .letter-foot .rule::after{content:"";position:absolute;left:50%;top:-3px;width:6px;height:6px;border:1px solid var(--magenta);background:var(--paper);transform:translateX(-50%) rotate(45deg)}
  .letter-foot .contact{font-family:"Marcellus",sans-serif;font-size:14.5px;color:#555;white-space:nowrap}
  .envelope{left:331px;top:536px;width:783px;height:340px;background:var(--paper)}
  .envelope .brand{left:38px;top:158px;width:140px}
  .envelope .mark{width:82px;height:82px}
  .envelope .name{font-size:28px;margin-top:4px}
  .envelope .tag{font-size:10px}
  .envelope .address{position:absolute;left:39px;top:292px;font-family:"Marcellus",sans-serif;font-size:17px;color:var(--magenta)}
  .card{width:346px;height:198px}
  .card-back{left:714px;top:240px;background:linear-gradient(160deg,#4f9aad 0%,#8a86a5 50%,#d55d95 100%);color:#fff;text-align:center}
  .card-back .frame{position:absolute;inset:6px;border:1px solid rgba(255,255,255,.85)}
  .card-back .frame::after{content:"";position:absolute;inset:4px;border:1px solid rgba(255,255,255,.55)}
  .corner{position:absolute;width:7px;height:7px}
  .card-back .corner{background:#fff}
  .card-front .corner{background:var(--magenta)}
  .c-tl{left:5px;top:5px}.c-tr{right:5px;top:5px}.c-bl{left:5px;bottom:5px}.c-br{right:5px;bottom:5px}
  .card-back .person{position:absolute;left:0;right:0;top:30px;font-family:"Marcellus",sans-serif;font-size:14px}
  .card-back .role{position:absolute;left:0;right:0;top:55px;font-size:7.5px}
  .diamond{position:absolute;left:50%;width:6px;height:6px;border:1px solid #fff;transform:translateX(-50%) rotate(45deg)}
  .card-back .line{position:absolute;left:0;right:0;font-size:7.5px;white-space:nowrap}
  .card-front{left:714px;top:464px;background:var(--paper)}
  .card-front .frame{position:absolute;inset:6px;border:1px solid var(--magenta)}
  .card-front .frame::after{content:"";position:absolute;inset:3px;border:1px solid var(--magenta)}
  .card-front .brand{left:0;right:0;top:52px}
  .card-front .mark{width:68px;height:68px}
  .card-front .name{font-size:22px;margin-top:2px}
  .card-front .tag{font-size:8px}
</style>
</head>
<body>

<div class="sheet backing"></div>

<section class="sheet letterhead">
  <div class="brand">
    <span class="mark"></span>
    <span class="name">LORVEX TILO</span>
    <span class="tag">Tilo rise</span>
  </div>

  <div class="letter">
    <p>To<br>The,<br>Director</p>
    <p>Lorem ipsum dolor sit amet, consectetur adipiscing elit. Sed at ante. Mauris eleifend, quam a vulp-<br>tate dictum, massa quam dapibus leo, eget vulputate orci purus ut lorem. In fringilla mi in ligula.<br>Pellen tesque aliquam quam vel dolor. Nunc adipiscing. Sed quamodio, tempus ac, aliquam mole-<br>tie varius ac, tellus. Vestibulum ut nulla aliquam risus rutrum interdum. Pellentesque lorem.</p>
    <p>Curabitur sit amet &nbsp;erat<br>venenatis non, arcu. &nbsp;Nunc<br>Curabitur dolonunc,eget<br>Vestibulum ante ipsum<br>orci vel mauris blandit</p>
    <p>In hac habitasse platea<br>dolor, sed imperdiet nulla<br>erat sit amet, elit.</p>
  </div>

  <div class="signoff">Thanking you,</div>
  <div class="signature" role="img" aria-label="Handwritten signature"></div>

  <footer class="letter-foot">
    <div class="company">Lorvex Tilo Medical Cannabis Cultivation</div>
    <div class="rule"></div>
    <div class="contact">555-014-2389 | www.lorvextilo.com | mara@lorvextilo.com | Dummy city, Dummy country land</div>
  </footer>
</section>

<section class="sheet envelope">
  <div class="brand">
    <span class="mark"></span>
    <span class="name">LORVEX TILO</span>
    <span class="tag">Tilo rise</span>
  </div>
  <div class="address">Dummy city, Dummy country land</div>
</section>

<section class="sheet card card-back">
  <div class="frame"></div>
  <span class="corner c-tl"></span><span class="corner c-tr"></span><span class="corner c-bl"></span><span class="corner c-br"></span>
  <div class="person">MARA QUELL</div>
  <div class="role">Director</div>
  <span class="diamond" style="top:77px"></span>
  <div class="line" style="top:97px">555-014-2389</div>
  <div class="line" style="top:115px">www.lorvextilo.com | mara@lorvextilo.com</div>
  <span class="diamond" style="top:138px"></span>
  <div class="line" style="top:162px">Lorvex Tilo medical cannabis cultivation</div>
  <div class="line" style="top:179px">Dummy city, Dummy country land</div>
</section>

<section class="sheet card card-front">
  <div class="frame"></div>
  <span class="corner c-tl"></span><span class="corner c-tr"></span><span class="corner c-bl"></span><span class="corner c-br"></span>
  <div class="brand">
    <span class="mark"></span>
    <span class="name">LORVEX TILO</span>
    <span class="tag">Tilo rise</span>
  </div>
</section>

</body>
</html>
```